Dynamic Business Card for Sports Supplements Company

Hi! I'm looking for an awesome business card to match my existing sports supplement company. I have uploaded my current company logo and screenshot of the front page of my website.

I would like to have something dynamic and interesting and utilize the colors in the website - the reds and purples

The business card should be double sided and focus on a unique eye-catching design on the back and include all the relevant company info.

Most importantly, it should say somewhere: "Sign up on our website for a coupon code."

Target Market(s)

Mostly for women gym goers but it shouldn't be too feminine. It should be in keeping with the website design. It should flow and clearly be connected to it

Industry/Entity Type

Business

Contact Information for Business Card

Lorraine K. Vestal
CEO
LVestal@Quorvanexco.com
www.quorvanexco.com
555.417.3820
P.O. Box 47315
Corvale, Westmark 00000

Sign up on our website for a coupon code

Font styles to use
Serif
Sans Serif
Other font styles liked:
• Novecento font family and "Quorvanex" is in AR Destine font

Requirements
Must have
• One side should be a bold Quorvanex logo design. Even just the symbol itself may be o.k. (see attached file)

```html
<!DOCTYPE html>
<html lang="en">
<head>
<meta charset="utf-8">
<title>Quorvanex Business Card</title>
<link rel="stylesheet" href="https://fonts.googleapis.com/css2?family=Michroma&family=Open+Sans:wght@400;600&display=swap">
<style>
  :root {
    --red: #e0262b;
    --black: #1b1b1d;
    --ink: #222224;
    --white: #ffffff;
    --stage: #e9e7e4;
    --stripe: #242426;
    --band-grey: #d4d4d6;
    --tag-grey: #d8d8d8;
  }
  * { margin: 0; padding: 0; box-sizing: border-box; }
  html, body { width: 1200px; height: 1200px; overflow: hidden; }
  body {
    background: var(--stage);
    font-family: "Open Sans", Arial, sans-serif;
    color: var(--ink);
    position: relative;
  }
  .card {
    position: absolute;
    left: 150px;
    width: 900px;
    height: 514px;
    overflow: hidden;
    box-shadow: 0 10px 28px rgba(0,0,0,0.18);
  }

  /* Back side */
  .card-back {
    top: 56px;
    background: repeating-linear-gradient(180deg, var(--black) 0 6px, var(--stripe) 6px 8px);
    color: var(--white);
    text-align: center;
  }
  .back-brand {
    position: absolute;
    top: 190px; left: 0; right: 0;
    display: flex; justify-content: center; align-items: center;
    gap: 16px;
  }
  .brand-mark { width: 26px; height: 26px; background: var(--red); flex: none; }
  .brand-name {
    font-family: "Michroma", sans-serif;
    font-size: 44px;
    letter-spacing: 2px;
    line-height: 1;
  }
  .back-tagline {
    position: absolute;
    top: 250px; left: 0; right: 0;
    font-family: "Michroma", sans-serif;
    font-size: 13px;
    letter-spacing: 3px;
    text-transform: uppercase;
    color: var(--tag-grey);
  }
  .back-signup {
    position: absolute;
    top: 300px; left: 0; right: 0;
    font-size: 21px;
  }
  .back-signup .accent { color: var(--red); }

  /* Front side */
  .card-front { top: 630px; background: var(--white); }
  .front-shapes { position: absolute; inset: 0; }
  .holder { position: absolute; left: 90px; top: 30px; }
  .holder-name {
    font-family: "Michroma", sans-serif;
    font-size: 25px;
    font-weight: 400;
    letter-spacing: 2px;
    color: var(--red);
    text-transform: uppercase;
    white-space: nowrap;
  }
  .holder-role {
    font-family: "Michroma", sans-serif;
    font-size: 15px;
    margin-top: 4px;
  }
  .contact-list {
    position: absolute;
    left: 52px; top: 206px;
    list-style: none;
    font-size: 18px;
  }
  .contact-list li {
    display: flex; align-items: center; gap: 12px;
    height: 30px; white-space: nowrap;
  }
  .contact-list svg { width: 16px; height: 16px; flex: none; }
  .front-brand {
    position: absolute;
    left: 420px; top: 188px;
    width: 440px;
    display: flex; flex-direction: column; align-items: center;
  }
  .front-brand .brand-row { display: flex; align-items: center; gap: 14px; }
  .front-brand .brand-name { color: var(--black); font-size: 40px; }
  .front-brand .brand-mark { width: 22px; height: 22px; }
  .front-tagline {
    margin-top: 10px;
    font-family: "Michroma", sans-serif;
    font-size: 12px;
    letter-spacing: 3px;
    text-transform: uppercase;
  }
  .address {
    position: absolute;
    right: 60px; top: 318px;
    text-align: right;
    font-style: normal;
    font-size: 22px;
    line-height: 1.45;
    letter-spacing: 0.5px;
    white-space: nowrap;
  }
</style>
</head>
<body>

<section class="card card-back" aria-label="Card back">
  <div class="back-brand">
    <span class="brand-mark"></span>
    <span class="brand-name">QUORVANEX</span>
  </div>
  <p class="back-tagline">Your Training Companion</p>
  <p class="back-signup"><span class="accent">Sign up</span> on our website for a coupon code</p>
</section>

<section class="card card-front" aria-label="Card front">
  <svg class="front-shapes" viewBox="0 0 900 514" width="900" height="514" aria-hidden="true">
    <polygon points="0,18 40,18 0,58" fill="var(--red)"/>
    <polygon points="40,18 78,18 78,58 0,58" fill="var(--black)"/>
    <polygon points="0,300 330,300 314,318 0,318" fill="var(--red)"/>
    <polygon points="330,300 346,300 400,438 384,438" fill="var(--band-grey)"/>
    <polygon points="384,438 900,438 900,514 420,514" fill="var(--black)"/>
  </svg>

  <div class="holder">
    <h1 class="holder-name">Lorraine K. Vestal</h1>
    <p class="holder-role">CEO</p>
  </div>

  <ul class="contact-list">
    <li>
      <svg viewBox="0 0 16 16"><path d="M3 1h3l1.5 4-2 1.2a9 9 0 0 0 4.3 4.3l1.2-2 4 1.5v3a2 2 0 0 1-2 2A13 13 0 0 1 1 3a2 2 0 0 1 2-2z" fill="var(--red)"/></svg>
      555.417.3820
    </li>
    <li>
      <svg viewBox="0 0 16 16"><rect x="1" y="3" width="14" height="10" fill="var(--red)"/><path d="M1 3l7 6 7-6" fill="none" stroke="#fff" stroke-width="1.4"/></svg>
      LVestal@Quorvanexco.com
    </li>
    <li>
      <svg viewBox="0 0 16 16"><circle cx="8" cy="8" r="7" fill="var(--red)"/><path d="M1 8h14M8 1c-3 3.5-3 10.5 0 14M8 1c3 3.5 3 10.5 0 14" fill="none" stroke="#fff" stroke-width="1"/></svg>
      www.quorvanexco.com
    </li>
  </ul>

  <div class="front-brand">
    <div class="brand-row">
      <span class="brand-mark"></span>
      <span class="brand-name">QUORVANEX</span>
    </div>
    <p class="front-tagline">Your Training Companion</p>
  </div>

  <address class="address">
    P.O. Box 47315<br>
    Corvale, Westmark 00000
  </address>
</section>

</body>
</html>
```